Home Staging Company needs business card design

We're a home staging company called Brightly Settled Home Staging. We would like a business card design that includes aqua and gray. Our current logo of house within chair is fine but I find we almost always use the logo in one color. I'll upload images of front and back of our current card and our logo. Note that we have dropped "Solutions" from our company name and don't want to include it on the card.

Target Market(s)

Realtors and homeowners - people interested in selling their homes

Contact Information for Business Card

Marisol Thistlewood
Brightly Settled Home Staging
757-555-0193
www.brightlysettled.com
marisol@brightlysettled.com

Font styles to use
Serif
Script

Requirements
Must have
• My logo and contact details
• UPDATE***
• I forgot to say that the company name should be included on the front of the card somehow.

```html
<!DOCTYPE html>
<html lang="en">
<head>
<meta charset="utf-8">
<title>Brightly Settled Home Staging – Business Card</title>
<link rel="stylesheet" href="https://fonts.googleapis.com/css2?family=Playfair+Display:wght@400&family=Roboto+Condensed:wght@400&family=Questrial&display=swap">
<style>
  :root {
    --backdrop: #c4c4c4;
    --charcoal: #363a3e;
    --paper: #f2f2f2;
    --aqua: #4aaab2;
    --aqua-text: #55b8c0;
    --edge-shadow: #2f3236;
    --ink: #3b3e42;
    --light: #f4f4f4;
  }
  * { box-sizing: border-box; margin: 0; padding: 0; }
  html, body { width: 1200px; height: 576px; overflow: hidden; }
  body { background: var(--backdrop); position: relative; }

  .card {
    position: absolute;
    top: 138px;
    width: 484px;
    height: 294px;
    border-radius: 12px;
    overflow: hidden;
  }

  /* Front */
  .card-front { left: 82px; background: var(--charcoal); }
  .front-name {
    position: absolute;
    left: 0; right: 0; top: 108px;
    text-align: center;
    font-family: "Playfair Display", serif;
    font-weight: 400;
    color: var(--light);
  }
  .front-name .line-main { display: block; font-size: 36px; line-height: 1.1; }
  .front-name .line-sub { display: block; font-size: 14px; letter-spacing: 0.42em; margin-top: 8px; padding-left: 0.42em; }
  .front-web {
    position: absolute;
    left: 0; right: 0; bottom: 12px;
    text-align: center;
    font-family: "Questrial", sans-serif;
    font-size: 12.5px;
    color: var(--aqua-text);
  }

  /* Back */
  .card-back { left: 602px; background: var(--paper); }
  .back-bands { position: absolute; inset: 0; }
  .back-name {
    position: absolute;
    left: 0; width: 205px; top: 176px;
    text-align: center;
    font-family: "Playfair Display", serif;
    font-weight: 400;
    color: var(--ink);
  }
  .back-name .line-main { display: block; font-size: 19px; line-height: 1.1; }
  .back-name .line-sub { display: block; font-size: 8.5px; letter-spacing: 0.4em; margin-top: 5px; padding-left: 0.4em; }

  .person { position: absolute; left: 258px; top: 74px; color: var(--light); }
  .person-name { font-family: "Roboto Condensed", sans-serif; font-size: 19.5px; line-height: 1.2; }
  .person-title { font-family: "Questrial", sans-serif; font-size: 10.5px; margin-top: 4px; }

  .contacts { position: absolute; left: 262px; top: 164px; list-style: none; }
  .contacts li {
    display: flex; align-items: center; height: 17.5px;
    font-family: "Questrial", sans-serif; font-size: 12px; color: var(--light);
  }
  .contacts svg { width: 10px; height: 10px; margin-right: 9px; flex: none; }
</style>
</head>
<body>

<section class="card card-front">
  <h1 class="front-name">
    <span class="line-main">Brightly Settled</span>
    <span class="line-sub">HOME STAGING</span>
  </h1>
  <p class="front-web">www.brightlysettled.com</p>
</section>

<section class="card card-back">
  <svg class="back-bands" viewBox="0 0 484 294" preserveAspectRatio="none" aria-hidden="true">
    <path d="M193 0 Q252 150 196 294 L484 294 L484 0 Z" fill="var(--edge-shadow)"/>
    <path d="M196 0 Q258 146 208 294 L484 294 L484 0 Z" fill="var(--aqua)"/>
  </svg>

  <h2 class="back-name">
    <span class="line-main">Brightly Settled</span>
    <span class="line-sub">HOME STAGING</span>
  </h2>

  <div class="person">
    <p class="person-name">Marisol Thistlewood</p>
    <p class="person-title">Managing Director</p>
  </div>

  <ul class="contacts">
    <li>
      <svg viewBox="0 0 10 10" aria-hidden="true"><path d="M1 3 Q5 0 9 3 L8 4.5 L6.5 3.8 L6.5 3 Q5 2.5 3.5 3 L3.5 3.8 L2 4.5 Z M2.5 5 L7.5 5 L8.5 9 L1.5 9 Z" fill="var(--light)"/></svg>
      757-555-0193
    </li>
    <li>
      <svg viewBox="0 0 10 10" aria-hidden="true"><g fill="none" stroke="var(--light)" stroke-width="0.9"><circle cx="5" cy="5" r="4.2"/><ellipse cx="5" cy="5" rx="1.8" ry="4.2"/><path d="M0.8 5 H9.2"/></g></svg>
      www.brightlysettled.com
    </li>
    <li>
      <svg viewBox="0 0 10 10" aria-hidden="true"><rect x="0.5" y="2" width="9" height="6.5" fill="var(--light)"/><path d="M0.5 2 L5 5.8 L9.5 2" fill="none" stroke="var(--aqua)" stroke-width="0.9"/></svg>
      marisol@brightlysettled.com
    </li>
  </ul>
</section>

</body>
</html>
```